New eyelid plastic surgery office needs a business card design-Eyelid Care Partners of the Brenton

I recently used PixelForge for my logo design and was very pleased with creativity and results. It was a difficult decision for me. Now I would like to create a business card based on this logo, which I will attach.

The text should be easily legible as some of my patients have difficulty seeing, but I would like a subtle, sophisticated artistry also evident to make the card memorable. Would like the card based on a similar color scheme as the logo but the inverse or other complementary colors may prove interesting
Updates

A good question was asked...my concern about my visually impaired patients was really my desire to avoid italicized or calligraphic type fonts that may be hard to read. Standard font size for a business card would be fine. Thanks!

Thank you so much for the great work so far. I wanted to give you my particular contact information to see if that would change the look of the cards. Martin Delacourt, MD Address: 2718 Harborview Lane, Suite 206 Wilmington, NC 28517 Phone: 910-555-0193 Fax: 910-555-0194 Website: www.brentonlidstudio.example Please delete the email slot from the card. Thanks so much!

Industry/Entity Type

Plastic

```html
<!DOCTYPE html>
<html lang="en">
<head>
<meta charset="utf-8">
<title>Eyelid Care Partners of the Brenton — Business Card</title>
<link href="https://fonts.googleapis.com/css2?family=Arimo:wght@700&display=swap" rel="stylesheet">
<style>
  :root {
    --page-bg: #ece9df;
    --card-light: #e6e6e6;
    --card-mid: #b9b9b9;
    --card-dark: #8a8a8a;
    --brand-blue: #1d4f9e;
    --ink: #111111;
    --rule: #333333;
  }
  html, body {
    margin: 0;
    width: 1200px;
    height: 888px;
    overflow: hidden;
    background: var(--page-bg);
    font-family: "Arimo", Arial, sans-serif;
  }
  .card {
    position: absolute;
    left: 75px;
    top: 144px;
    width: 1050px;
    height: 600px;
    overflow: hidden;
    background: var(--card-mid);
    box-shadow: 0 6px 18px rgba(0,0,0,0.25);
  }
  .card-backdrop {
    position: absolute;
    inset: 0;
  }
  .brand-name {
    position: absolute;
    left: 0;
    right: 0;
    top: 100px;
    text-align: center;
    color: var(--brand-blue);
    font-weight: 700;
    text-transform: uppercase;
    line-height: 1;
    margin: 0;
  }
  .brand-name .line-main {
    display: block;
    font-size: 62px;
    letter-spacing: 1px;
  }
  .brand-name .line-sub {
    display: block;
    font-size: 31px;
    margin-top: 10px;
    letter-spacing: 1px;
  }
  .contact {
    position: absolute;
    left: 78px;
    top: 345px;
    padding-left: 18px;
    border-left: 2px solid var(--rule);
    color: var(--ink);
    font-weight: 700;
  }
  .contact-heading {
    font-size: 22px;
    margin: 0 0 8px;
  }
  .doctor-name {
    font-size: 33px;
    margin: 0 0 12px 180px;
    white-space: nowrap;
  }
  .details {
    display: grid;
    grid-template-columns: 112px auto;
    row-gap: 2px;
    font-size: 22px;
    margin: 0;
  }
  .details dt, .details dd { margin: 0; white-space: nowrap; }
</style>
</head>
<body>
  <article class="card">
    <svg class="card-backdrop" width="1050" height="600" viewBox="0 0 1050 600">
      <defs>
        <radialGradient id="top-glow" cx="0.5" cy="0.25" r="0.7">
          <stop offset="0" stop-color="#d8d8d8"/>
          <stop offset="1" stop-color="#8e8e8e"/>
        </radialGradient>
        <linearGradient id="lower-band" x1="0" y1="0" x2="0" y2="1">
          <stop offset="0" stop-color="#d2d2d2"/>
          <stop offset="1" stop-color="#bdbdbd"/>
        </linearGradient>
      </defs>
      <rect width="1050" height="600" fill="url(#top-glow)"/>
      <path d="M0 160 Q525 380 1050 240 L1050 600 L0 600 Z" fill="#c9c9c9" opacity="0.7"/>
      <path d="M0 250 Q525 470 1050 270 L1050 600 L0 600 Z" fill="url(#lower-band)"/>
      <path d="M250 520 Q650 360 980 590 Q640 430 250 520 Z" fill="#e4e4e4" opacity="0.8"/>
    </svg>

    <h1 class="brand-name">
      <span class="line-main">Eyelid Care Partners</span>
      <span class="line-sub">of the Brenton</span>
    </h1>

    <section class="contact">
      <p class="contact-heading">Contact &nbsp;:</p>
      <p class="doctor-name">Martin Delacourt, MD</p>
      <dl class="details">
        <dt>Address</dt><dd>: 2718 Harborview Lane, Suite 206 Wilmington, NC 28517</dd>
        <dt>Phone</dt><dd>: 910 - 555 - 0193</dd>
        <dt>Fax</dt><dd>: 910 - 555 - 0194</dd>
        <dt>web</dt><dd>: www.brentonlidstudio.example</dd>
      </dl>
    </section>
  </article>
</body>
</html>
```